Food Hall in Harbor Point, CA by the Pacific Ocean that has 15 vendors and 2 bars

We need a web page design that highlights our food hall in Harbor Point, CA. The name of the food hall is Calloway Food Hall. Inside of the food hall there are 15 different vendors and 2 bars. The place has a beautiful patio and it is by Pacific Ocean. Most of the vendors are local to San Clemente area. The highly anticipated location is opening during the summer of 2025. Website should have a dropdown menu for the different vendors that are in the food hall and people should be able to click to their respective business website. The website should also include link to our social media channels and also a link to provide comments and subscribe for the mailing list.
Target Market(s)
Mostly residents in the Harbor Point, CA and surrounding areas. Couples, families and tourist alike that are looking for an exceptional dining experience that everyone can find something they like.
Industry/Entity Type
Restaurants
Coding
Number of Pages Required
Font styles to use
Look and feel

```html
<!DOCTYPE html>
<html lang="en">
<head>
<meta charset="utf-8">
<title>Calloway Food Hall – Harbor Point</title>
<link href="https://fonts.googleapis.com/css2?family=Montserrat:wght@500;700;800&family=Mulish:wght@400;600;700&display=swap" rel="stylesheet">
<style>
:root{
  --navy:#0b3f9c;
  --blue:#0d72c6;
  --drinks:#1266b3;
  --ink:#1a1a1a;
  --text:#3b3b3b;
  --soft:#f2f1f3;
  --card:#e3ecf5;
  --white:#ffffff;
}
*{margin:0;padding:0;box-sizing:border-box}
html,body{width:1200px;height:4918px;overflow:hidden}
body{position:relative;background:var(--white);font-family:"Mulish",sans-serif;color:var(--text)}
.abs{position:absolute}
h1,h2,h3,.brand,.btn,.nav a{font-family:"Montserrat",sans-serif}
.btn{position:absolute;display:flex;align-items:center;justify-content:center;background:var(--blue);color:var(--white);font-weight:700;font-size:14px;text-transform:uppercase;letter-spacing:.3px;text-decoration:none}
.rule{position:absolute;height:3px;width:46px;background:var(--white)}
.rule.blue{background:var(--navy)}
.photo{position:absolute}

/* header */
.site-header{position:absolute;top:0;left:0;width:1200px;height:100px;background:var(--white);z-index:3}
.logo-badge{position:absolute;left:152px;top:10px;width:118px;height:118px;border-radius:50%;background:var(--white);box-shadow:0 2px 6px rgba(0,0,0,.15);display:flex;align-items:center;justify-content:center;z-index:4}
.logo-badge span{width:96px;height:96px;border-radius:50%;background:linear-gradient(160deg,#8fc1e6,#d9e6ee 55%,#c9744c)}
.brand{position:absolute;left:291px;top:25px;font-size:19px;font-weight:800;line-height:23px;color:var(--ink);text-transform:uppercase}
.nav{position:absolute;top:29px;left:515px;display:flex}
.nav a{font-size:13.5px;font-weight:500;color:var(--ink);text-decoration:none;height:33px;display:flex;align-items:center;margin-right:32px}
.nav a.active{background:var(--blue);color:var(--white);padding:0 14px;margin-right:18px}

/* hero */
.hero{position:absolute;top:100px;left:0;width:1200px;height:580px}
.hero h1{position:absolute;left:151px;top:272px;font-size:44px;line-height:50px;font-weight:800;color:var(--white);text-transform:uppercase}
.hero p{position:absolute;left:151px;top:384px;width:400px;font-size:21px;line-height:31px;color:var(--white)}
.dots{position:absolute;display:flex;gap:18px}
.hero .dots span{width:22px;height:4px;background:var(--white)}
.hero .dots span.on{background:var(--blue)}

/* about */
.about-line{position:absolute;left:177px;top:773px;width:3px;height:725px;background:var(--navy)}
.about-tag{position:absolute;left:146px;top:800px;transform:rotate(-90deg);font-family:"Montserrat",sans-serif;font-size:12px;font-weight:700;color:var(--navy);letter-spacing:1px}
.about-title{position:absolute;left:215px;top:774px;font-size:26px;line-height:33px;font-weight:800;color:var(--ink);text-transform:uppercase}
.about-copy{position:absolute;left:215px;top:882px;width:255px;font-size:13px;line-height:19.5px}
.feature{position:absolute;top:1250px;width:230px}
.feature svg{display:block;height:50px}
.feature h3{margin-top:38px;font-size:17px;font-weight:800;color:var(--ink)}
.feature p{margin-top:10px;font-size:12.5px;line-height:18.5px;width:215px}
.divider{position:absolute;top:1250px;width:2px;height:248px;background:var(--navy)}

/* split bands */
.band h2{position:absolute;font-size:30px;font-weight:800;color:var(--white);text-transform:uppercase}
.band p{position:absolute;font-size:13px;line-height:18.5px;color:var(--white)}

/* vendors */
.vendors-title{position:absolute;top:2640px;left:0;width:1200px;text-align:center;font-size:30px;font-weight:800;color:var(--ink);text-transform:uppercase}
.track{position:absolute;top:2765px;left:0;width:1200px;height:458px;overflow:hidden}
.vcard{position:absolute;top:0;width:280px;height:458px;background:var(--card)}
.vcard.active{border:3px solid var(--blue)}
.vcard .mark{position:absolute;left:27px;top:30px;width:226px;height:226px}
.vcard h3{position:absolute;left:30px;top:292px;font-size:17px;font-weight:800;color:var(--ink);text-transform:uppercase;white-space:nowrap}
.vcard p{position:absolute;left:30px;top:324px;width:220px;font-size:12.5px;line-height:18px}
.vcard .btn{left:30px;top:393px;width:139px;height:36px;font-size:12.5px}
.vdots span{width:9px;height:9px;border-radius:50%;background:#d5dbe3}
.vdots span.on{background:var(--navy)}

/* spot */
.spot-bg{position:absolute;left:630px;top:3345px;width:570px;height:460px;background:var(--soft)}
.spot h2{position:absolute;left:675px;top:3402px;font-size:30px;font-weight:800;color:var(--ink);text-transform:uppercase}
.spot p{position:absolute;left:675px;top:3495px;width:335px;font-size:13.5px;line-height:21px}

/* dining */
.dining-box{position:absolute;left:149px;top:3934px;width:442px;height:359px;background:var(--soft)}
.dining h2{position:absolute;left:193px;top:3970px;font-size:29px;line-height:36px;font-weight:800;color:var(--ink);text-transform:uppercase}
.dining p{position:absolute;left:195px;top:4083px;width:355px;font-size:13.5px;line-height:21px}

/* newsletter + footer */
.footer-bg{position:absolute;left:0;top:4516px;width:1200px;height:402px;background:var(--navy)}
.newsletter{position:absolute;left:147px;top:4400px;width:904px;height:189px;border:8px solid var(--navy);background:var(--white)}
.newsletter h2{position:absolute;left:80px;top:84px;font-size:26px;line-height:30px;font-weight:800;color:var(--navy);text-transform:uppercase}
.field{position:absolute;top:32px;width:242px;height:48px;border:2px solid var(--navy);font-size:13px;font-weight:600;color:var(--navy);padding:0 18px;display:flex;align-items:center}
.subscribe{position:absolute;left:332px;top:102px;width:501px;height:54px;background:var(--blue);color:var(--white);font-family:"Montserrat",sans-serif;font-weight:800;font-size:25px;display:flex;align-items:center;justify-content:center;text-transform:uppercase}
.f-logo{position:absolute;left:149px;top:4650px;width:105px;height:105px;border-radius:50%;background:var(--white);display:flex;align-items:center;justify-content:center}
.f-logo span{width:90px;height:90px;border-radius:50%;background:linear-gradient(160deg,#8fc1e6,#d9e6ee 55%,#c9744c)}
.f-brand{position:absolute;left:279px;top:4672px;font-size:19px;line-height:23px;font-weight:700;color:var(--white);text-transform:uppercase;font-family:"Montserrat",sans-serif}
.f-head{position:absolute;top:4642px;font-family:"Montserrat",sans-serif;font-size:16px;font-weight:700;color:var(--white);text-transform:uppercase}
.f-contact{position:absolute;left:470px;font-size:13px;color:var(--white);display:flex;align-items:center;gap:18px}
.f-menu{position:absolute;left:748px;top:4670px;list-style:none}
.f-menu li{font-size:13px;line-height:19.5px;color:var(--white)}
.social{position:absolute;left:884px;top:4715px;display:flex;gap:5px}
.social span{width:26px;height:26px;border-radius:50%;background:var(--white)}
.f-line{position:absolute;left:149px;top:4818px;width:902px;height:1px;background:rgba(255,255,255,.35)}
.copy{position:absolute;top:4858px;left:0;width:1200px;text-align:center;font-size:12px;color:var(--white)}
</style>
</head>
<body>

<header class="site-header">
  <nav class="nav">
    <a class="active" href="#">HOME</a>
    <a href="#">ABOUT US</a>
    <a href="#">VENDORS</a>
    <a href="#">BARS</a>
    <a href="#">MENU</a>
    <a href="#">CONTACT US</a>
  </nav>
  <div class="brand">Calloway<br>Food Hall</div>
</header>
<div class="logo-badge"><span></span></div>

<section class="hero">
  <div class="photo" style="inset:0;background:linear-gradient(180deg,rgba(60,50,70,.2),rgba(30,28,34,.55)),linear-gradient(90deg,#4a3b49,#6b5560 50%,#3e3b42)" role="img" aria-label="Interior of the food hall with vendor counters and seating"></div>
  <h1>Food Hall in<br>Harbor Point</h1>
  <p>Lorem Ipsum is simply dummy has been the industr text of the printing</p>
  <a class="btn" href="#" style="left:151px;top:465px;width:146px;height:42px">Read More</a>
  <div class="dots" style="left:534px;top:535px"><span class="on"></span><span></span><span></span><span></span></div>
</section>

<section class="about">
  <div class="about-line"></div>
  <div class="about-tag">ABOUT</div>
  <h2 class="about-title">Calloway<br>Food Hall</h2>
  <p class="about-copy">Lorem ipsum dolor sit amet, consectetur adipiscing elit, sed do eiusmod tempor incididunt ut labore et dolore magna aliqua. Ut enim ad minim veniam, quis nostrud exercitation ullamco laboris nisi ut aliquip ex ea commodo consequat. Duis aute irure dolor in reprehenderit in voluptate velit esse cillum dolore eu fugiat</p>
  <a class="btn" href="#" style="left:219px;top:1091px;width:126px;height:37px;font-size:12.5px">Read More</a>
  <div class="photo" style="left:523px;top:744px;width:528px;height:446px;background:linear-gradient(180deg,#3c4a78 0%,#252838 55%,#6b4a2c 100%)" role="img" aria-label="Food hall building exterior at dusk with lit sign"></div>

  <div class="feature" style="left:223px">
    <svg viewBox="0 0 40 50" width="40" fill="none" stroke="#0d72c6" stroke-width="2"><rect x="4" y="4" width="32" height="10"/><path d="M4 14 Q10 20 14 14 Q20 20 26 14 Q30 20 36 14"/><rect x="6" y="18" width="28" height="28"/><circle cx="20" cy="30" r="6"/><path d="M14 46v-6h12v6"/></svg>
    <h3>VENDORS</h3>
    <p>Lorem ipsum dolor sit amet, consectetur adipiscing elit, sed do eiusmod tempor incididunt ut labore et dolore magna aliqua. Ut enim ad minim veniam</p>
  </div>
  <div class="divider" style="left:473px"></div>
  <div class="feature" style="left:521px">
    <svg viewBox="0 0 40 50" width="40" fill="none" stroke="#0d72c6" stroke-width="2"><path d="M4 8h32L20 28z"/><path d="M20 28v16M12 46h16"/><circle cx="30" cy="6" r="4"/><path d="M30 2l-6 12"/></svg>
    <h3>BAR</h3>
    <p>Lorem ipsum dolor sit amet, consectetur adipiscing elit, sed do eiusmod tempor incididunt ut labore et dolore magna aliqua. Ut enim ad minim veniam</p>
  </div>
  <div class="divider" style="left:778px"></div>
  <div class="feature" style="left:836px">
    <svg viewBox="0 0 44 50" width="44" fill="none" stroke="#0d72c6" stroke-width="2"><path d="M4 44l10-24 14 14z"/><path d="M9 32l8 8M12 25l10 10"/><path d="M24 16q4-6 10-4M28 24q6-2 10 2M30 6l2 3M38 14l3-1M20 8l1 3"/><circle cx="36" cy="6" r="1.5"/><circle cx="40" cy="22" r="1.5"/></svg>
    <h3>CELEBRATE</h3>
    <p>Lorem ipsum dolor sit amet, consectetur adipiscing elit, sed do eiusmod tempor incididunt ut labore et dolore magna aliqua. Ut enim ad minim veniam</p>
  </div>
</section>

<section class="band">
  <div class="photo" style="left:0;top:1555px;width:620px;height:511px;background:radial-gradient(circle at 35% 55%,#d8d2c4 0%,#8a7b68 30%,#2f2a26 70%)" role="img" aria-label="Close-up of a sushi roll held with chopsticks"></div>
  <div class="abs" style="left:620px;top:1555px;width:580px;height:511px;background:var(--navy)"></div>
  <h2 style="left:679px;top:1604px">Great Food</h2>
  <div class="rule" style="left:681px;top:1662px"></div>
  <p style="left:683px;top:1700px;width:345px">Lorem ipsum dolor sit amet, consectetur adipiscing elit, sed do eiusmod tempor incididunt ut labore et dolore magna aliqua. Ut enim ad minim veniam.</p>
  <p style="left:683px;top:1773px;width:345px">Sed ut perspiciatis unde omnis iste natus error sit voluptatem accusantium doloremque laudantium, totam rem aperiam, eaque ipsa quae ab illo inventore veritatis et quasi architecto beatae vitae dicta.</p>
  <p style="left:683px;top:1864px;width:345px">At vero eos et accusamus et iusto odio dignissimos ducimus qui blanditiis praesentium voluptatum deleniti atque corrupti quos dolores et quas molestias excepturi sint occaecati</p>
  <a class="btn" href="#" style="left:685px;top:1965px;width:128px;height:37px;font-size:12.5px">Read More</a>

  <div class="abs" style="left:0;top:2066px;width:620px;height:512px;background:var(--drinks)"></div>
  <h2 style="left:170px;top:2152px">Amazing Drinks</h2>
  <div class="rule" style="left:172px;top:2211px"></div>
  <p style="left:172px;top:2248px;width:335px">Lorem ipsum dolor sit amet, consectetur adipiscing elit, sed do eiusmod tempor incididunt ut labore et dolore magna aliqua. Ut enim ad minim veniam.</p>
  <p style="left:172px;top:2321px;width:335px">Sed ut perspiciatis unde omnis iste natus error sit voluptatem accusantium doloremque laudantium, totam rem aperiam, eaque ipsa quae ab illo inventore veritatis et quasi architecto beatae vitae dicta.</p>
  <a class="btn" href="#" style="left:174px;top:2431px;width:126px;height:37px;font-size:12.5px">Read More</a>
  <div class="photo" style="left:620px;top:2066px;width:580px;height:512px;background:linear-gradient(135deg,#2c2a2a 0%,#5a4638 45%,#1e1c1c 100%)" role="img" aria-label="Bartender pouring a cocktail into a martini glass"></div>
</section>

<section class="vendors">
  <h2 class="vendors-title">Discover Our Vendors</h2>
  <div class="rule blue" style="left:577px;top:2706px"></div>
  <div class="track">
    <div class="vcard" style="left:-156px">
      <div class="mark"></div>
      <h3>Sweet Cone</h3>
      <p>Lorem ipsum dolor sit amet, conse ctetur adipiscing elit, sed do eiusmod tempor.</p>
      <a class="btn" href="#">See the Menu</a>
    </div>
    <div class="vcard" style="left:149px">
      <div class="mark" style="display:flex;align-items:center;justify-content:center"><span style="font-family:Montserrat,sans-serif;font-weight:800;font-size:22px;color:var(--ink)">NOODLE LANTERN</span></div>
      <h3>Noodle Lantern</h3>
      <p>Lorem ipsum dolor sit amet, conse ctetur adipiscing elit, sed do eiusmod tempor.</p>
      <a class="btn" href="#">See the Menu</a>
    </div>
    <div class="vcard active" style="left:456px">
      <div class="mark" style="left:24px;top:27px;display:flex;align-items:center;justify-content:center"><span style="font-family:Montserrat,sans-serif;font-weight:800;font-size:22px;color:var(--ink)">ORBIT BURGER</span></div>
      <h3 style="left:27px;top:289px">Orbit Burger</h3>
      <p style="left:27px;top:321px">Lorem ipsum dolor sit amet, conse ctetur adipiscing elit, sed do eiusmod tempor.</p>
      <a class="btn" href="#" style="left:27px;top:390px">See the Menu</a>
    </div>
    <div class="vcard" style="left:773px">
      <div class="mark" style="background:#111;display:flex;align-items:center;justify-content:center"><span style="font-family:Montserrat,sans-serif;font-weight:800;font-size:24px;color:var(--white)">EMBER BIRD</span></div>
      <h3>Ember Bird</h3>
      <p>Lorem ipsum dolor sit amet, conse ctetur adipiscing elit, sed do eiusmod tempor.</p>
      <a class="btn" href="#">See the Menu</a>
    </div>
    <div class="vcard" style="left:1074px">
      <div class="mark"></div>
      <h3>Noodle Lantern</h3>
      <p>Lorem ipsum dolor sit amet, conse ctetur adipiscing elit, sed do eiusmod tempor.</p>
      <a class="btn" href="#">See the Menu</a>
    </div>
  </div>
  <div class="dots vdots" style="left:555px;top:3269px;gap:11px"><span class="on"></span><span></span><span></span><span></span><span></span></div>
</section>

<section class="spot">
  <div class="photo" style="left:0;top:3345px;width:630px;height:460px;background:linear-gradient(120deg,#6b6a4a 0%,#b89a78 40%,#4a3a2e 100%)" role="img" aria-label="Friends sharing a meal at a restaurant table"></div>
  <div class="spot-bg"></div>
  <h2>Your Go To Spot</h2>
  <div class="rule blue" style="left:677px;top:3456px"></div>
  <p>Lorem ipsum dolor sit amet, consectetur adipiscing elit, sed do eiusmod tempor incididunt ut labore et dolore magna aliqua. Ut enim ad minim veniam. Sed ut perspiciatis unde omnis iste natus error sit voluptatem accusantium doloremque laudantium, totam rem aperiam, eaque ipsa quae ab illo inventore veritatis et quasi architecto beatae vitae dicta.</p>
  <a class="btn" href="#" style="left:681px;top:3692px;width:146px;height:42px">Read More</a>
</section>

<section class="dining">
  <div class="photo" style="left:458px;top:3877px;width:593px;height:450px;background:linear-gradient(135deg,#4a6aa0 0%,#d8c49a 45%,#b8884e 75%,#3e5a8a 100%)" role="img" aria-label="Stacked wraps filled with grilled meat and greens"></div>
  <div class="dining-box"></div>
  <h2>Dining Experiences<br>for Food Lovers</h2>
  <p>Lorem ipsum dolor sit amet, consectetur adipiscing elit, sed do eiusmod tempor incididunt ut labore et dolore magna aliqua. Ut enim ad minim veniam. Sed ut perspiciatis unde omnis iste natus error sit voluptatem accusantium doloremque laudantium.</p>
  <a class="btn" href="#" style="left:197px;top:4213px;width:147px;height:42px">Read More</a>
</section>

<footer>
  <div class="footer-bg"></div>
  <div class="newsletter">
    <svg class="abs" style="left:80px;top:28px" width="40" height="40" viewBox="0 0 40 40"><rect x="6" y="4" width="28" height="24" fill="#0d72c6"/><path d="M2 16v22h36V16L20 28z" fill="#0b3f9c"/><path d="M11 11h18M11 17h18" stroke="#fff" stroke-width="2"/></svg>
    <h2>Newsletter<br>Subscribe</h2>
    <div class="field" style="left:332px">Full Name</div>
    <div class="field" style="left:589px">Email id</div>
    <div class="subscribe">Subscribe</div>
  </div>

  <div class="f-logo"><span></span></div>
  <div class="f-brand">Calloway<br>Food Hall</div>

  <div class="f-head" style="left:470px">Contact</div>
  <div class="f-contact" style="top:4677px"><svg width="12" height="16" viewBox="0 0 12 16"><path d="M6 0a6 6 0 0 0-6 6c0 4.5 6 10 6 10s6-5.5 6-10a6 6 0 0 0-6-6zm0 8.5A2.5 2.5 0 1 1 6 3.5a2.5 2.5 0 0 1 0 5z" fill="#fff"/></svg>Harbor Point, CA</div>
  <div class="f-contact" style="top:4713px"><svg width="13" height="13" viewBox="0 0 16 16"><path d="M3 0l3 4-2 2c1 2 4 5 6 6l2-2 4 3-2 3C7 16 0 9 0 3z" fill="#fff"/></svg>(949) 555 0142</div>
  <div class="f-contact" style="top:4750px"><svg width="14" height="11" viewBox="0 0 16 12"><rect width="16" height="12" fill="#fff"/><path d="M0 0l8 6 8-6" stroke="#0b3f9c" stroke-width="1.5" fill="none"/></svg>info@callowayfoodhall.com</div>

  <div class="f-head" style="left:748px">Menu</div>
  <ul class="f-menu">
    <li>Home</li><li>About us</li><li>Vendors</li><li>Bars</li><li>Menu</li><li>Contact us</li>
  </ul>

  <div class="f-head" style="left:884px">Follow Us</div>
  <div class="social"><span aria-label="Social channel one"></span><span aria-label="Social channel two"></span><span aria-label="Social channel three"></span></div>

  <div class="f-line"></div>
  <div class="copy">Copyright © 2025 All Rights Reserved</div>
</footer>

</body>
</html>
```